Natural Light/Organic/Documentary Photography Business

I like a simple, approachable, feminine, earthy/organic feel. Earth/neutral tones, nothing too loud or obnoxious. I like the watercolor look. I don't want anything too trendy or something I'll get tired of after a couple months. As far as colors, I am much more a fan of cream/taupe/blue/green...not a fan of pink or purple at all.

Target Market(s)

Weddings & Families

Industry/Entity Type

Wedding Photography

Contact Information for Business Card

website, email, phone number

Font styles to use
Other font styles liked:
• Horizontes, Gotham

Colors

Designer to choose colors to be used in the design.

Requirements
Must have
• Website: www.mirelhatchway.com
• Phone: 418.629.5073
• Email: mirel@mirelhatchway.com
Nice to have
• I like the watercolor look but its not necessary. I like simple/earthy tones. Nothing too loud or distracting. Simple & feminine without being too girly. I like an approachable/soft feel.
• Instagram: www.instagram.com/mirelhatchwayphotography/
Should not have
• NO loud colors or design or pattern. I do not want a photo of a camera or lens or anything cheesy like that.

```html
<!DOCTYPE html>
<html lang="en">
<head>
<meta charset="utf-8">
<title>Mirel Hatchway Photography – Business Card</title>
<link rel="stylesheet" href="https://fonts.googleapis.com/css2?family=Ephesis&family=Montserrat:wght@400&family=Oswald:wght@300&display=swap">
<style>
  :root {
    --paper: #f8f5ef;
    --ink: #6f6260;
    --sage-soft: #d3ddd0;
    --mist: #c4cbc2;
  }
  html, body {
    margin: 0;
    padding: 0;
    width: 1200px;
    height: 678px;
    overflow: hidden;
    background: var(--paper);
  }
  .card {
    position: relative;
    width: 1200px;
    height: 678px;
    background: var(--paper);
    overflow: hidden;
  }
  .artwork {
    position: absolute;
    inset: 0;
    background: linear-gradient(100deg, var(--paper) 0%, var(--paper) 45%, var(--sage-soft) 75%, var(--mist) 100%);
  }
  .brand {
    position: absolute;
    left: 0;
    right: 0;
    top: 212px;
    text-align: center;
    color: var(--ink);
  }
  .brand-name {
    margin: 0;
    font-family: "Ephesis", cursive;
    font-weight: 400;
    font-size: 128px;
    line-height: 1;
    letter-spacing: 3px;
  }
  .brand-tagline {
    margin: -6px 0 0;
    font-family: "Montserrat", sans-serif;
    font-size: 19px;
    line-height: 1;
    letter-spacing: 15px;
    padding-left: 15px;
  }
  .contact {
    position: absolute;
    left: 102px;
    top: 592px;
    margin: 0;
    padding: 0;
    list-style: none;
    font-family: "Oswald", sans-serif;
    font-weight: 300;
    font-size: 35px;
    line-height: 1;
    color: var(--ink);
    white-space: nowrap;
  }
  .contact li { position: absolute; top: 0; }
  .contact-phone { left: 0; }
  .contact-email, .contact-web { font-variant: small-caps; text-transform: lowercase; }
  .contact-email { left: 227px; }
  .contact-web { left: 667px; }
  .contact-label { text-transform: capitalize; }
</style>
</head>
<body>
<main class="card">
  <div class="artwork" role="img" aria-label="Soft sage green and grey watercolor washes with faint cream leaf shapes"></div>

  <header class="brand">
    <h1 class="brand-name">Mirel Hatchway</h1>
    <p class="brand-tagline">PHOTOGRAPHY</p>
  </header>

  <ul class="contact">
    <li class="contact-phone">418.629.5073</li>
    <li class="contact-email"><span class="contact-label">Email:</span>mirel@mirelhatchway.com</li>
    <li class="contact-web"><span class="contact-label">Web:</span>www.mirelhatchway.com</li>
  </ul>
</main>
</body>
</html>
```